Cocktail-Making Assistant App re-design

Ok boys and girls, here's the deal:
I have an android app which is almost complete, but needs a design overhaul.

The app is a standard cocktail-making assistant: gives you a list of cocktails and the ability to see which cocktail you can make out of those ingredients (drinks, fruit, etc) you have at home.

I've attached some general app flow, as well as detailed requirements/explanation presentation. Most of those things are just FYI, so that you know what it's about.

3 screens are the most important (main screen, cocktail view screen, ingredient view screen), meaning I will pick the design mostly based on ideas for those 3 things, with the fourth being a rather simple list (given on attached flow, third tier)
Some other screens are derived from that, with some minor changes on it, but you shouldn't care about that.

There are lots of other, non-explained things which I said nothing about only because they are (from design point of view) completely the same and would only make it seem more complicated.

I don't want to influence the colour scheme, but the app will be released under RedFig developer name (having a light colured red fig as a logo) so I suppose some brownish design, for example, will not really fit nicely. If you, however, have a killer which you are confident will prove me wrong, I'm looking forward to seeing it!

It should be a serious, elegant look (as opposed to cartoonish, but we are not aiming for a business look at all!), not cluttered with details, no clubbing themes, glitter and so on.

Test apk file available on request (Android 2.3+).

Edit: payment is now guaranteed
Also please note that currently, the favorite, "heart" button has a motion effect:
on click it flies out of the screen to the left (white heart) and comes back to the screen as a red heart. Take that into consideration, if it means anything to you.

Target Market(s)

Whoever you imagine would enjoy drinking cocktails

Industry/Entity Type

Business

Requirements
Must have
• Everything is said in the provided documentation - images say more than I could possibly write here.
Nice to have
• As said, most of the icons are a nice-to-have. Only those which are critically linked to the rest of the design must be provided. More details in the docs.
Should not have
• No cartoon look, No zillion colours

```html
<!DOCTYPE html>
<html lang="en">
<head>
<meta charset="utf-8">
<title>Cocktail Search</title>
<link rel="stylesheet" href="https://fonts.googleapis.com/css2?family=Roboto:wght@300;400;700&display=swap">
<style>
:root{
  --page:#e8edf1;
  --header-top:#8ee5fb;
  --header-bottom:#76d6f2;
  --back-bg:#5ec8ea;
  --arrow:#2d8fc2;
  --title-dark:#1e5877;
  --title-light:#3a9bc9;
  --body-top:#5da9c1;
  --body-bottom:#0a2438;
  --search-bg:#3f8eae;
  --search-btn:#4b98b9;
  --placeholder:#98e4f7;
  --list-bg:#f2f2f2;
  --divider:#dcdcdc;
  --name:#474747;
  --star:#155ea6;
  --star-empty:#9a9a9a;
  --meta:#6a6a6a;
  --count:#2b6ca8;
  --ready:#5aa832;
}
*{box-sizing:border-box;margin:0;padding:0}
html,body{width:960px;height:1200px;overflow:hidden;background:var(--page)}
body{font-family:"Roboto",sans-serif;font-weight:300;position:relative}
.screen{
  position:absolute;left:30px;top:0;width:480px;height:640px;
  transform:scale(1.875);transform-origin:0 0;overflow:hidden;
  background:linear-gradient(180deg,var(--body-top) 0%,#2f6f8a 45%,var(--body-bottom) 100%);
}
.app-bar{
  position:absolute;left:0;top:0;width:480px;height:70px;
  background:linear-gradient(180deg,var(--header-top),var(--header-bottom));
  box-shadow:0 2px 4px rgba(0,0,0,.15);
}
.back-button{
  position:absolute;left:0;top:0;width:80px;height:70px;background:var(--back-bg);
  display:flex;align-items:center;justify-content:center;
}
.app-title{
  position:absolute;left:80px;right:0;top:0;height:70px;line-height:66px;
  text-align:center;font-size:28px;font-weight:300;color:var(--title-dark);padding-right:80px;
}
.app-title span{color:var(--title-light)}
.search-field{
  position:absolute;left:20px;top:88px;width:440px;height:60px;
  background:var(--search-bg);border-radius:3px;
  box-shadow:inset 0 1px 3px rgba(0,0,0,.2);
}
.search-placeholder{
  position:absolute;left:27px;top:0;line-height:58px;font-size:19px;color:var(--placeholder);
}
.search-button{
  position:absolute;right:0;top:0;width:60px;height:60px;background:var(--search-btn);
  border-radius:0 3px 3px 0;display:flex;align-items:center;justify-content:center;
  border-left:1px solid rgba(0,0,0,.08);
}
.cocktail-list{
  position:absolute;left:20px;top:161px;width:440px;height:440px;
  background:var(--list-bg);border-radius:3px;overflow:hidden;list-style:none;
  box-shadow:0 3px 10px rgba(0,0,0,.3);
}
.cocktail{position:relative;height:80px;border-bottom:1px solid var(--divider)}
.cocktail.is-cut{opacity:.35}
.thumb{position:absolute;left:10px;top:10px;width:70px;height:60px;border-radius:2px}
.thumb.bushwacker{background:linear-gradient(135deg,#c98a52,#e9d8c0 55%,#7cc6d6)}
.thumb.belmont{background:radial-gradient(circle at 50% 45%,#d8303a 0,#c01f2c 28%,#f5f5f5 52%,#fff 100%)}
.thumb.shade{background:radial-gradient(circle at 50% 50%,#a3142a 0,#5b1a22 30%,#2c2a28 70%)}
.thumb.blank{background:#c9c9c9}
.name{position:absolute;left:99px;top:12px;font-size:24px;color:var(--name)}
.rating{position:absolute;left:97px;top:47px;display:flex;gap:7.5px}
.rating svg{width:20px;height:20px}
.stock{position:absolute;right:19px;top:50px;font-size:14px;color:var(--meta);display:flex;align-items:center;gap:6px}
.stock b{color:var(--count);font-weight:700}
.stock .of{color:var(--meta)}
.stock.ready{color:var(--ready)}
</style>
</head>
<body>
<svg width="0" height="0" style="position:absolute">
  <defs>
    <polygon id="star-shape" points="10,1.5 12.6,7.2 18.8,7.8 14.1,12 15.5,18.2 10,15 4.5,18.2 5.9,12 1.2,7.8 7.4,7.2"/>
    <clipPath id="left-half"><rect x="0" y="0" width="10" height="20"/></clipPath>
  </defs>
</svg>

<main class="screen">
  <header class="app-bar">
    <div class="back-button">
      <svg width="30" height="26" viewBox="0 0 30 26"><path d="M13 3 L3 13 L13 23 M4 13 H27" fill="none" stroke="var(--arrow)" stroke-width="5" stroke-linecap="round" stroke-linejoin="round"/></svg>
    </div>
    <h1 class="app-title">Cocktail <span>Search</span></h1>
  </header>

  <div class="search-field">
    <div class="search-placeholder">Search All Categories</div>
    <div class="search-button">
      <svg width="30" height="30" viewBox="0 0 30 30"><circle cx="13" cy="13" r="9" fill="none" stroke="#fff" stroke-width="3"/><path d="M20 20 L27 27" stroke="#fff" stroke-width="3.5" stroke-linecap="round"/></svg>
    </div>
  </div>

  <ul class="cocktail-list">
    <li class="cocktail">
      <div class="thumb bushwacker" role="img" aria-label="Photo of a creamy Florida Bushwacker cocktail"></div>
      <div class="name">151 Florida Bushwacker</div>
      <div class="rating">
        <svg viewBox="0 0 20 20"><use href="#star-shape" fill="var(--star)"/></svg>
        <svg viewBox="0 0 20 20"><use href="#star-shape" fill="var(--star)"/></svg>
        <svg viewBox="0 0 20 20"><use href="#star-shape" fill="none" stroke="var(--star-empty)"/><use href="#star-shape" fill="var(--star)" clip-path="url(#left-half)"/></svg>
        <svg viewBox="0 0 20 20"><use href="#star-shape" fill="none" stroke="var(--star-empty)"/></svg>
        <svg viewBox="0 0 20 20"><use href="#star-shape" fill="none" stroke="var(--star-empty)"/></svg>
      </div>
      <div class="stock">You have: <span><b>4</b> <span class="of">of 8</span></span></div>
    </li>
    <li class="cocktail">
      <div class="thumb belmont" role="img" aria-label="Photo of a red Belmont cocktail in a glass"></div>
      <div class="name">Belmont</div>
      <div class="rating">
        <svg viewBox="0 0 20 20"><use href="#star-shape" fill="var(--star)"/></svg>
        <svg viewBox="0 0 20 20"><use href="#star-shape" fill="none" stroke="var(--star-empty)"/></svg>
        <svg viewBox="0 0 20 20"><use href="#star-shape" fill="none" stroke="var(--star-empty)"/></svg>
        <svg viewBox="0 0 20 20"><use href="#star-shape" fill="none" stroke="var(--star-empty)"/></svg>
        <svg viewBox="0 0 20 20"><use href="#star-shape" fill="none" stroke="var(--star-empty)"/></svg>
      </div>
      <div class="stock">You have: <b>7 of 8</b></div>
    </li>
    <li class="cocktail">
      <div class="thumb shade" role="img" aria-label="Photo of the In The Shade cocktail with a lime slice"></div>
      <div class="name">In The Shade</div>
      <div class="rating">
        <svg viewBox="0 0 20 20"><use href="#star-shape" fill="var(--star)"/></svg>
        <svg viewBox="0 0 20 20"><use href="#star-shape" fill="var(--star)"/></svg>
        <svg viewBox="0 0 20 20"><use href="#star-shape" fill="var(--star)"/></svg>
        <svg viewBox="0 0 20 20"><use href="#star-shape" fill="var(--star)"/></svg>
        <svg viewBox="0 0 20 20"><use href="#star-shape" fill="none" stroke="var(--star-empty)"/></svg>
      </div>
      <div class="stock ready">
        <svg width="16" height="12" viewBox="0 0 16 12"><path d="M1.5 6 L6 10.5 L14.5 1.5" fill="none" stroke="var(--ready)" stroke-width="2.2" stroke-linecap="round" stroke-linejoin="round"/></svg>
        You have: <b>8 of 8</b>
      </div>
    </li>
    <li class="cocktail">
      <div class="thumb bushwacker" role="img" aria-label="Photo of a creamy Florida Bushwacker cocktail"></div>
      <div class="name">151 Florida Bushwacker</div>
      <div class="rating">
        <svg viewBox="0 0 20 20"><use href="#star-shape" fill="var(--star)"/></svg>
        <svg viewBox="0 0 20 20"><use href="#star-shape" fill="var(--star)"/></svg>
        <svg viewBox="0 0 20 20"><use href="#star-shape" fill="none" stroke="var(--star-empty)"/><use href="#star-shape" fill="var(--star)" clip-path="url(#left-half)"/></svg>
        <svg viewBox="0 0 20 20"><use href="#star-shape" fill="none" stroke="var(--star-empty)"/></svg>
        <svg viewBox="0 0 20 20"><use href="#star-shape" fill="none" stroke="var(--star-empty)"/></svg>
      </div>
      <div class="stock">You have: <span><b>4</b> <span class="of">of 8</span></span></div>
    </li>
    <li class="cocktail">
      <div class="thumb belmont" role="img" aria-label="Photo of a red Belmont cocktail in a glass"></div>
      <div class="name">Belmont</div>
      <div class="rating">
        <svg viewBox="0 0 20 20"><use href="#star-shape" fill="var(--star)"/></svg>
        <svg viewBox="0 0 20 20"><use href="#star-shape" fill="none" stroke="var(--star-empty)"/></svg>
        <svg viewBox="0 0 20 20"><use href="#star-shape" fill="none" stroke="var(--star-empty)"/></svg>
        <svg viewBox="0 0 20 20"><use href="#star-shape" fill="none" stroke="var(--star-empty)"/></svg>
        <svg viewBox="0 0 20 20"><use href="#star-shape" fill="none" stroke="var(--star-empty)"/></svg>
      </div>
      <div class="stock">You have: <span><b>7</b> <span class="of">of 8</span></span></div>
    </li>
    <li class="cocktail is-cut">
      <div class="thumb blank" role="img" aria-label="Photo of the In The Shade cocktail"></div>
      <div class="name">In The Shade</div>
    </li>
  </ul>
</main>
</body>
</html>
```